Every Shelf Set Neatly or ESN Organized needs a business card design. ESN Organized is a professi

We need a business card design that is clean, sharp and conveys a sense of organization. I already have a logo.

Target Market(s)

Families (specifically mothers), small business owners, parents, seniors

Industry/Entity Type

Business

Contact Information for Business Card

My website is www.esnorganized-example.com and my Facebook page is http://www.sociallink-example.com/everyshelfsetneatly. The phone number is 418-552-7094 and I want to be listed as Lorna M. Pelham, Owner

Requirements
Must have
• My logo.

```html
<!DOCTYPE html>
<html lang="en">
<head>
<meta charset="utf-8">
<title>ESN Organized — Business Card</title>
<link rel="stylesheet" href="https://fonts.googleapis.com/css2?family=Open+Sans:wght@400;600&display=swap">
<style>
  :root {
    --stage: #e9e7e4;
    --card: #f7f7f7;
    --brand-blue: #1a7ad4;
    --ink: #1c1c1c;
    --shadow: rgba(0, 0, 0, 0.18);
  }
  * { margin: 0; padding: 0; box-sizing: border-box; }
  html, body {
    width: 1200px;
    height: 900px;
    overflow: hidden;
    background: var(--stage);
    font-family: "Open Sans", Arial, sans-serif;
  }
  .stage { position: relative; width: 1200px; height: 900px; }
  .card {
    position: absolute;
    background: var(--card);
    box-shadow: 0 6px 18px var(--shadow);
  }
  .card--front { left: 78px; top: 33px; width: 588px; height: 364px; }
  .card--back { left: 388px; top: 505px; width: 566px; height: 352px; }

  .brand-name {
    position: absolute;
    left: 32px;
    top: 84px;
    color: var(--brand-blue);
    font-weight: 400;
    font-size: 36px;
    letter-spacing: 1px;
    line-height: 1;
  }
  .owner { position: absolute; left: 32px; top: 190px; }
  .owner__name {
    color: var(--brand-blue);
    font-weight: 600;
    font-size: 20px;
    line-height: 1.2;
  }
  .owner__title { color: var(--ink); font-size: 15px; margin-top: 2px; }

  .contact-list { position: absolute; left: 32px; top: 262px; list-style: none; }
  .contact-list li {
    display: flex;
    align-items: center;
    gap: 7px;
    color: var(--ink);
    font-size: 15px;
    height: 24.5px;
  }
  .contact-list svg { width: 11px; height: 11px; fill: var(--brand-blue); flex: none; }

  .back-mark {
    position: absolute;
    right: 60px;
    top: 170px;
    color: var(--brand-blue);
    font-weight: 400;
    font-size: 100px;
    letter-spacing: 2px;
    line-height: 1;
  }
  .social-link {
    position: absolute;
    right: 22px;
    bottom: 30px;
    color: var(--brand-blue);
    font-weight: 600;
    font-size: 14px;
  }
</style>
</head>
<body>
<main class="stage">
  <section class="card card--front" aria-label="Business card front">
    <div class="brand-name">ESN Organized</div>
    <div class="owner">
      <div class="owner__name">Lorna M. Pelham</div>
      <div class="owner__title">Owner</div>
    </div>
    <ul class="contact-list">
      <li>
        <svg viewBox="0 0 12 12" aria-hidden="true"><path d="M2.5 0.5l2 2.2-1 1.4c.7 1.6 2 2.9 3.6 3.6l1.4-1 2.2 2-1.3 2.3C4.6 11.5.5 7.4.2 2.1z"/></svg>
        <span>418-552-7094</span>
      </li>
      <li>
        <svg viewBox="0 0 12 12" aria-hidden="true"><path d="M0 2h12v1L6 7 0 3zM0 4.3l6 4 6-4V10H0z"/></svg>
        <span>info@esnorganized-example.com</span>
      </li>
      <li>
        <svg viewBox="0 0 12 12" aria-hidden="true"><circle cx="6" cy="6" r="6"/><path d="M1 6h10M6 1c-2 2.6-2 7.4 0 10M6 1c2 2.6 2 7.4 0 10" stroke="#f7f7f7" stroke-width="0.9" fill="none"/></svg>
        <span>www.esnorganized-example.com</span>
      </li>
    </ul>
  </section>

  <section class="card card--back" aria-label="Business card back">
    <div class="back-mark">ESN</div>
    <div class="social-link">www.sociallink-example.com/everyshelfsetneatly</div>
  </section>
</main>
</body>
</html>
```